BrivoTerna. Lantern of the Steady Harvest. Business card

Professional business card for BrivoTerna (Lantern of the Steady Harvest)
My rationale: Strategy-> Execution-> Results-> Value that lead to the BrivoTerna name: We put the Lantern of the Steady Harvest.
We deliver value to our customers helping them at defining a good strategy (cyan arrow). 90% of well formulated strategies fail due to poor execution so we also consider strategical execution very important (green arrow). Due to the execution we obtain the results (blue arrow). Finally, the results provide feedback to redefine strategy, and the new strategy has to be executed and new results obtained providing new feedback and on and on. It's like a wheel that finally, must create corporate value: value for shareholders, staholders, employees, providers...-

Target Market(s)

CEOs and steering comitees , invewrnent funds

Industry/Entity Type

Business Consultant

Contact Information for Business Card

Teodoro Vinsquel
CEO & Founder
teodoro.vinsquel@brivoterna-example.com
Mobile: +34 655.803.912
www.brivoterna-example.com

Colors

Designer to choose colors to be used in the design.

Requirements
Nice to have
• Nice to hace the words: Strategy, execution, results
• Nice to vave the claim: Lantern of the Steady Harvest
• The three colors should be shown:
• cyan for STRATEGY
• green for EXECUTION
• blue for RESULTS
Should not have
• Complete black background

```html
<!DOCTYPE html>
<html lang="en">
<head>
<meta charset="utf-8">
<title>BrivoTerna — Business Card</title>
<link rel="stylesheet" href="https://fonts.googleapis.com/css2?family=Open+Sans:wght@400;600;700&display=swap">
<style>
  :root {
    --brand-blue: #243e8c;
    --brand-green: #9bc93a;
    --brand-cyan: #27ace2;
    --paper: #ffffff;
    --backdrop: #2c2c2e;
  }
  * { box-sizing: border-box; margin: 0; padding: 0; }
  html, body { width: 1200px; height: 900px; overflow: hidden; }
  body {
    background: var(--backdrop);
    font-family: "Open Sans", sans-serif;
    position: relative;
  }
  .card {
    position: absolute;
    left: 260px;
    width: 680px;
    height: 390px;
    overflow: hidden;
    box-shadow: 0 10px 30px rgba(0,0,0,.45);
  }
  .card--back { top: 40px; background: var(--brand-blue); }
  .card--front { top: 470px; background: var(--paper); }

  .back-name {
    position: absolute;
    left: 70px;
    top: 70px;
    font-weight: 700;
    font-size: 64px;
    color: var(--paper);
    letter-spacing: -1px;
  }
  .back-bands { position: absolute; inset: 0; }

  .front-band { position: absolute; inset: 0; }
  .front-name {
    position: absolute;
    left: 48px;
    top: 72px;
    display: flex;
    align-items: center;
    gap: 12px;
    font-weight: 700;
    font-size: 44px;
    color: var(--brand-blue);
    letter-spacing: -1px;
  }
  .front-name__dot {
    width: 20px; height: 20px; border-radius: 50%;
    background: var(--brand-green);
  }
  .person {
    position: absolute;
    right: 50px;
    top: 112px;
    text-align: right;
  }
  .person__name {
    font-weight: 700;
    font-size: 24px;
    letter-spacing: 1.5px;
    color: var(--brand-blue);
    text-transform: uppercase;
  }
  .person__role {
    font-size: 17px;
    color: var(--brand-green);
    letter-spacing: .5px;
  }
  .contacts {
    position: absolute;
    right: 36px;
    top: 256px;
    list-style: none;
    text-align: right;
    color: var(--paper);
  }
  .contacts__item {
    display: flex;
    justify-content: flex-end;
    align-items: center;
    gap: 12px;
    font-size: 16px;
    line-height: 25px;
  }
  .contacts__icon { width: 18px; height: 18px; flex: none; }
  .tagline {
    position: absolute;
    right: 66px;
    top: 342px;
    font-size: 17px;
    letter-spacing: .5px;
    text-transform: uppercase;
    color: var(--paper);
  }
</style>
</head>
<body>

  <section class="card card--back" aria-label="Card back">
    <svg class="back-bands" viewBox="0 0 680 390" aria-hidden="true">
      <path d="M0,390 L0,372 C200,350 420,330 680,300 L680,390 Z" fill="var(--brand-cyan)"/>
      <path d="M0,372 C200,350 420,330 680,300 L680,318 C420,348 200,368 0,390 Z" fill="var(--brand-green)"/>
    </svg>
    <div class="back-name">BrivoTerna</div>
  </section>

  <section class="card card--front" aria-label="Card front">
    <svg class="front-band" viewBox="0 0 680 390" aria-hidden="true">
      <polygon points="0,268 680,198 680,390 0,390" fill="var(--brand-green)"/>
      <polygon points="0,280 680,210 680,390 0,390" fill="var(--brand-blue)"/>
    </svg>

    <div class="front-name"><span class="front-name__dot"></span>BrivoTerna</div>

    <div class="person">
      <p class="person__name">Teodoro Vinsquel</p>
      <p class="person__role">CEO &amp; Founder</p>
    </div>

    <ul class="contacts">
      <li class="contacts__item">+34 655.803.912
        <svg class="contacts__icon" viewBox="0 0 20 20" aria-hidden="true"><circle cx="10" cy="10" r="8.5" fill="none" stroke="var(--brand-green)" stroke-width="1.6"/><path d="M7,6 L9,8.5 L8,9.5 C8.6,11 9.4,11.8 10.8,12.2 L11.8,11.2 L14,13 L13,14.3 C9.5,14.3 6,10.8 6,7.2 Z" fill="var(--brand-green)"/></svg>
      </li>
      <li class="contacts__item">teodoro.vinsquel@brivoterna-example.com
        <svg class="contacts__icon" viewBox="0 0 20 20" aria-hidden="true"><rect x="2" y="4.5" width="16" height="11" fill="none" stroke="var(--brand-green)" stroke-width="1.6"/><path d="M2,4.5 L10,11 L18,4.5" fill="none" stroke="var(--brand-green)" stroke-width="1.6"/></svg>
      </li>
      <li class="contacts__item">www.brivoterna-example.com
        <svg class="contacts__icon" viewBox="0 0 20 20" aria-hidden="true"><circle cx="10" cy="10" r="8" fill="none" stroke="var(--brand-green)" stroke-width="1.6"/><ellipse cx="10" cy="10" rx="3.5" ry="8" fill="none" stroke="var(--brand-green)" stroke-width="1.4"/><path d="M2,10 H18 M3.5,6 H16.5 M3.5,14 H16.5" stroke="var(--brand-green)" stroke-width="1.4"/></svg>
      </li>
    </ul>

    <p class="tagline">Lantern of the Steady Harvest</p>
  </section>

</body>
</html>
```